Chartered Professional Accounting Firm Needs a Business Card Design

We need a card design for an accounting firm based in Toronto, Ontario. The firm name is Pavel Ostrom Professional Corporation. The owner of the firm is a chartered professional accountant and a certified general accountant. Services of the firm include 60% tax preparation and consulting and 40% financial statements for corporation year-end. We would like a modern design. The color could be black, white, gray, blue or other color to bring more confidence to clients. The logo of the firm should be included in the design. Thanks

Name: Pavel Ostrom, CPA, CGA Address: 47 Maple Crest Rd. Richmond Hill, ON L7K 3B5 Telephone: (416) 562-3907 Fax:(416) 734-2165 Email: pavel@pavelostrom-example.ca

Accounting

```html
<!DOCTYPE html>
<html lang="en">
<head>
<meta charset="utf-8">
<title>Pavel Ostrom Professional Corporation – Business Card</title>
<link href="https://fonts.googleapis.com/css2?family=Oswald:wght@500&family=Cinzel:wght@600&family=Open+Sans:wght@400;600&display=swap" rel="stylesheet">
<style>
  :root {
    --page-bg: #e6e6e8;
    --brand-blue: #33379a;
    --brand-blue-deep: #23267a;
    --brand-blue-light: #4a4fb8;
    --band-gray: #8a8a8f;
    --text-gray: #6b6b72;
    --text-dark: #3a3a40;
    --card-white: #ffffff;
    --card-white-shade: #ececef;
  }
  * { margin: 0; padding: 0; box-sizing: border-box; }
  html, body {
    width: 1200px; height: 871px; overflow: hidden;
    background: var(--page-bg);
  }
  .stage { position: relative; width: 1200px; height: 871px; }

  .card {
    position: absolute;
    width: 540px; height: 309px;
    border-radius: 4px;
    overflow: hidden;
    box-shadow: 0 10px 28px rgba(0,0,0,.18);
  }

  /* Back of card */
  .card--back {
    left: 60px; top: 130px;
    background: linear-gradient(160deg, var(--brand-blue-light) 0%, var(--brand-blue) 45%, var(--brand-blue-deep) 100%);
  }
  .card--back .emblem-block {
    position: absolute; right: 46px; top: 34px;
    width: 170px; height: 170px;
    background: rgba(20, 22, 90, .28);
  }
  .card--back .lockup { position: absolute; left: 34px; bottom: 40px; }

  .lockup { display: flex; align-items: center; gap: 12px; }
  .lockup__mark { width: 40px; height: 40px; flex: none; }
  .lockup__name {
    font-family: "Oswald", sans-serif; font-weight: 500;
    font-size: 22px; line-height: 1; text-transform: uppercase; letter-spacing: .5px;
  }
  .lockup__firm-type { display: block; font-size: 12px; letter-spacing: .4px; margin-top: 2px; }
  .lockup__credentials {
    font-family: "Open Sans", sans-serif; font-weight: 400;
    font-size: 8px; line-height: 1.3; text-transform: uppercase; letter-spacing: .4px;
    margin-top: 3px; white-space: nowrap;
  }
  .card--back .lockup__mark { background: rgba(255,255,255,.9); }
  .card--back .lockup__name { color: #fff; }
  .card--back .lockup__credentials { color: rgba(255,255,255,.8); }

  /* Front of card */
  .card--front {
    left: 600px; top: 432px;
    background: linear-gradient(170deg, var(--card-white) 55%, var(--card-white-shade) 100%);
  }
  .card--front .lockup { position: absolute; left: 28px; top: 34px; }
  .card--front .lockup__mark { background: var(--brand-blue); }
  .card--front .lockup__name { color: var(--brand-blue); }
  .card--front .lockup__credentials { color: var(--text-gray); }

  .wave-band { position: absolute; left: 0; bottom: 0; width: 540px; height: 160px; }

  .contact { position: absolute; left: 300px; top: 34px; }
  .contact__name {
    font-family: "Cinzel", serif; font-weight: 600;
    font-size: 14px; letter-spacing: 1.5px; color: var(--brand-blue);
    margin-bottom: 12px; white-space: nowrap;
  }
  .contact__address, .contact__line {
    font-family: "Open Sans", sans-serif; font-size: 10.5px;
    letter-spacing: 1px; color: var(--text-dark); line-height: 1.55;
    white-space: nowrap;
  }
  .contact__address { margin-bottom: 8px; }
  .contact__line { display: flex; align-items: center; gap: 10px; }
  .contact__icon { width: 13px; height: 11px; flex: none; }
</style>
</head>
<body>
<main class="stage">

  <section class="card card--back" aria-label="Card back">
    <div class="emblem-block"></div>
    <div class="lockup">
      <div class="lockup__mark"></div>
      <div>
        <div class="lockup__name">Pavel Ostrom<span class="lockup__firm-type">Professional Corporation</span></div>
        <div class="lockup__credentials">Chartered Professional Accountant<br>Certified General Accountant</div>
      </div>
    </div>
  </section>

  <section class="card card--front" aria-label="Card front">
    <svg class="wave-band" viewBox="0 0 540 160" preserveAspectRatio="none" aria-hidden="true">
      <path d="M0 58 C150 66 300 92 400 128 C450 146 500 156 540 152 L540 160 L0 160 Z" fill="var(--band-gray)"/>
      <path d="M0 64 C150 72 300 98 400 134 C450 150 500 160 540 160 L0 160 Z" fill="#fff"/>
      <path d="M0 72 C140 80 290 106 390 140 C430 152 480 160 540 160 L0 160 Z" fill="var(--brand-blue)"/>
    </svg>

    <div class="lockup">
      <div class="lockup__mark"></div>
      <div>
        <div class="lockup__name">Pavel Ostrom<span class="lockup__firm-type">Professional Corporation</span></div>
        <div class="lockup__credentials">Chartered Professional Accountant<br>Certified General Accountant</div>
      </div>
    </div>

    <div class="contact">
      <div class="contact__name">Pavel Ostrom, CPA, CGA</div>
      <div class="contact__address">47 Maple Crest<br>Rd. Richmond Hill<br>ON L7K 3B5</div>
      <div class="contact__line">
        <svg class="contact__icon" viewBox="0 0 13 11" aria-label="Telephone"><path d="M1 3 Q6.5 -1 12 3 L10 4.5 L9 3 Q6.5 2 4 3 L3 4.5 Z" fill="var(--brand-blue)"/><rect x="3" y="5" width="7" height="5" rx="1" fill="var(--brand-blue)"/></svg>
        <span>(416) 562-3907</span>
      </div>
      <div class="contact__line">
        <svg class="contact__icon" viewBox="0 0 13 11" aria-label="Fax"><rect x="3.5" y="0.5" width="6" height="3" fill="none" stroke="var(--brand-blue)"/><rect x="1" y="3.5" width="11" height="5" rx="1" fill="var(--brand-blue)"/><rect x="3.5" y="7" width="6" height="3.5" fill="#fff" stroke="var(--brand-blue)"/></svg>
        <span>(416) 734-2165</span>
      </div>
      <div class="contact__line">
        <svg class="contact__icon" viewBox="0 0 13 11" aria-label="Email"><rect x="0.5" y="1.5" width="12" height="8" fill="var(--brand-blue)"/><path d="M0.5 1.5 L6.5 6 L12.5 1.5" fill="none" stroke="#fff" stroke-width="1"/></svg>
        <span>pavel@pavelostrom-example.ca</span>
      </div>
    </div>
  </section>

</main>
</body>
</html>
```